Business Card Design (NEW FILES)

ATTENTION: New vector files are available. Please update your design to reflect/use the new (better resolution) logo images.

Seeking a unique and professional business card design for a commercial drone photography/videography business. The layout should feature
the logo (attached) and include the following information:
Owen Tarrick
614-502-7738
www.skylarkreelworks.example
NRD Certified Remote Pilot

Owen Tarrick

```html
<!DOCTYPE html>
<html lang="en">
<head>
<meta charset="utf-8">
<title>Skylark Reelworks – Business Card</title>
<link rel="stylesheet" href="https://fonts.googleapis.com/css2?family=Montserrat:wght@500;700&family=Open+Sans:wght@400;600&display=swap">
<style>
  :root {
    --stage: #222222;
    --navy: #161a4a;
    --navy-deep: #12163f;
    --teal: #1bb3b5;
    --orange: #ec8a4a;
    --white: #ffffff;
    --ink: #1b1f52;
    --back-mark: #3c57b0;
  }
  * { margin: 0; padding: 0; box-sizing: border-box; }
  html, body {
    width: 1200px; height: 780px; overflow: hidden;
    background: var(--stage);
  }
  .stage {
    position: relative; width: 1200px; height: 780px;
    display: flex; align-items: center; justify-content: center; gap: 40px;
  }
  .card {
    position: relative; width: 540px; height: 309px; overflow: hidden;
    box-shadow: 0 12px 30px rgba(0,0,0,.45);
  }
  .card-front { background: var(--white); }
  .card-back { background: var(--navy-deep); }
  .swoosh { position: absolute; inset: 0; width: 100%; height: 100%; }

  .brand-name {
    position: absolute; left: 120px; top: 30px;
    font-family: "Montserrat", sans-serif; font-weight: 500;
    font-size: 26px; line-height: 1.05; letter-spacing: 1px;
    color: var(--ink); text-transform: uppercase;
    display: flex; align-items: center; gap: 10px;
  }
  .brand-dot {
    width: 14px; height: 14px; border-radius: 50%; background: var(--orange);
    flex: none;
  }
  .contact {
    position: absolute; left: 40px; top: 100px;
    font-family: "Open Sans", sans-serif; font-size: 12px; color: var(--ink);
    list-style: none;
  }
  .contact li { display: flex; align-items: center; gap: 8px; margin-bottom: 5px; }
  .contact svg { width: 11px; height: 11px; flex: none; }

  .person {
    position: absolute; right: 34px; top: 140px; text-align: right;
  }
  .person-name {
    font-family: "Montserrat", sans-serif; font-weight: 700; font-size: 26px;
    color: var(--ink); letter-spacing: .5px; line-height: 1.1;
  }
  .person-name .first { color: var(--orange); font-weight: 500; }
  .person-role {
    font-family: "Open Sans", sans-serif; font-size: 13px; color: var(--ink);
    margin-top: 2px;
  }
  .edge-tab {
    position: absolute; right: 0; top: 180px; width: 14px; height: 52px;
    background: var(--orange);
  }
  .credentials {
    position: absolute; left: 100px; top: 250px; width: 200px;
    font-family: "Open Sans", sans-serif; font-size: 13px; line-height: 1.45;
    color: var(--white); text-align: center;
  }

  .back-mark {
    position: absolute; inset: 0;
    display: flex; align-items: center; justify-content: center; gap: 14px;
    font-family: "Montserrat", sans-serif; font-weight: 500;
    font-size: 30px; letter-spacing: 2px; text-transform: uppercase;
    color: var(--back-mark);
  }
  .back-mark .brand-dot { width: 18px; height: 18px; background: var(--back-mark); }
</style>
</head>
<body>
<main class="stage">
  <section class="card card-front" aria-label="Business card front">
    <svg class="swoosh" viewBox="0 0 540 309" aria-hidden="true">
      <path d="M0 100 C 20 160, 100 200, 260 220 C 340 232, 400 262, 430 309 L 0 309 Z" fill="var(--navy)"/>
      <path d="M8 92 C 30 150, 108 190, 240 208" fill="none" stroke="var(--white)" stroke-width="5"/>
      <path d="M16 90 C 38 145, 112 182, 240 201" fill="none" stroke="var(--teal)" stroke-width="6"/>
      <path d="M262 213 C 345 225, 410 260, 442 309" fill="none" stroke="var(--orange)" stroke-width="8"/>
    </svg>

    <div class="brand-name"><span>Skylark<br>Reelworks</span><span class="brand-dot"></span></div>

    <ul class="contact">
      <li>
        <svg viewBox="0 0 12 12"><path d="M3 1 L5 3 L4 4.5 C4.6 6 6 7.4 7.5 8 L9 7 L11 9 L9.5 11 C5 10.5 1.5 7 1 2.5 Z" fill="var(--orange)"/></svg>
        614-502-7738
      </li>
      <li>
        <svg viewBox="0 0 12 12"><circle cx="6" cy="6" r="5" fill="var(--orange)"/><path d="M1 6 H11 M6 1 C3.5 4 3.5 8 6 11 M6 1 C8.5 4 8.5 8 6 11" stroke="var(--white)" stroke-width=".8" fill="none"/></svg>
        www.skylarkreelworks.example
      </li>
    </ul>

    <div class="person">
      <div class="person-name"><span class="first">Owen</span> Tarrick</div>
      <div class="person-role">Owner</div>
    </div>
    <div class="edge-tab"></div>

    <p class="credentials">NRD Certified Remote Pilot<br>Fully Insured</p>
  </section>

  <section class="card card-back" aria-label="Business card back">
    <div class="back-mark"><span>Skylark Reelworks</span><span class="brand-dot"></span></div>
  </section>
</main>
</body>
</html>
```